Seeking funky, innovative business cards

I am looking to refresh our current business cards to something more engaging, visual and impactful. We are a management consultancy firm, see website (www.larkstone-partners.com.au). I've included our colour scheme, sample of the slides we use and our old business cards. We would like our cards to have icons. The card should display:- Name- Title- Mobile number- Address- Email address- Website - Company logo- Our purpose statement "we shape the brightest teams in every city"

Contact Information for Business Card

Brennan Ulfsson
Consultant
0468 927 341
Level 3, 218 Wexley Street, Melbourne 3000
brennan@larkstone-partners.com.au
www.larkstone-partners.com.au

Purpose statement "we shape the brightest teams in every city"
LOGO available in google images

Font styles to use
Other font styles liked:
• Open Sans Light, Bebas Neue (open to other cool foints)

Colors
ffc214
5c5c5c
f5f5f5
fefefe

Requirements
Must have
• - Name
• - Title
• - Mobile number
• - Address
• - Email address
• - Website
• - Company logo
• - Our purpose statement "we shape the brightest teams in every city"
Nice to have
• - Icons
• - Colour (see our colour scheme"

```html
<!DOCTYPE html>
<html lang="en">
<head>
<meta charset="utf-8">
<title>Larkstone Partners – Business Card</title>
<link href="https://fonts.googleapis.com/css2?family=Roboto:ital,wght@0,300;0,400;0,500;1,400&display=swap" rel="stylesheet">
<style>
  :root {
    --backdrop: #b9b9b9;
    --card: #ffffff;
    --accent: #f9a825;
    --ink: #454a4c;
    --ink-soft: #555a5c;
    --rule: #9a9a9a;
  }
  html, body {
    margin: 0;
    padding: 0;
    width: 1200px;
    height: 1200px;
    overflow: hidden;
    background: var(--backdrop);
    font-family: "Roboto", Arial, sans-serif;
  }
  .card {
    position: absolute;
    left: 218px;
    width: 800px;
    height: 457px;
    background: var(--card);
  }
  .card--front { top: 115px; }
  .card--back { top: 638px; }

  .identity {
    position: absolute;
    right: 465px;
    top: 196px;
    text-align: right;
  }
  .identity__name {
    margin: 0;
    color: var(--accent);
    font-size: 30px;
    font-weight: 400;
    line-height: 36px;
    white-space: nowrap;
  }
  .identity__title {
    margin: 0;
    color: var(--ink);
    font-size: 20px;
    font-weight: 500;
    line-height: 26px;
  }
  .divider {
    position: absolute;
    left: 369px;
    top: 152px;
    width: 2px;
    height: 150px;
    background: linear-gradient(to bottom, rgba(154,154,154,0), var(--rule) 20%, var(--rule) 80%, rgba(154,154,154,0));
  }
  .contact {
    position: absolute;
    left: 400px;
    top: 157px;
    color: var(--ink-soft);
    font-size: 19px;
    font-weight: 400;
  }
  .contact__address {
    margin: 0 0 13px;
    line-height: 24px;
  }
  .contact__list {
    list-style: none;
    margin: 0;
    padding: 0;
  }
  .contact__item {
    display: flex;
    align-items: center;
    height: 25.5px;
    white-space: nowrap;
  }
  .contact__icon {
    width: 18px;
    height: 18px;
    margin-right: 13px;
    flex: none;
  }

  .brand {
    position: absolute;
    left: 0;
    right: 0;
    top: 215px;
    display: flex;
    justify-content: center;
    align-items: center;
    gap: 16px;
  }
  .brand__dot {
    width: 18px;
    height: 18px;
    border-radius: 50%;
    background: var(--accent);
  }
  .brand__name {
    color: var(--ink);
    font-size: 54px;
    font-weight: 400;
    letter-spacing: -0.5px;
    line-height: 1;
  }
  .purpose {
    position: absolute;
    left: 0;
    right: 0;
    top: 381px;
    margin: 0;
    text-align: center;
    font-size: 21px;
    font-style: italic;
    color: var(--ink-soft);
    white-space: nowrap;
  }
  .purpose__accent { color: var(--accent); }
</style>
</head>
<body>

<section class="card card--front">
  <div class="identity">
    <h1 class="identity__name">Brennan Ulfsson</h1>
    <p class="identity__title">Consultant</p>
  </div>

  <div class="divider"></div>

  <div class="contact">
    <p class="contact__address">Level 3, 218 Wexley Street,<br>Melbourne 3000</p>
    <ul class="contact__list">
      <li class="contact__item">
        <svg class="contact__icon" viewBox="0 0 24 24" aria-hidden="true"><path fill="var(--accent)" d="M6.6 10.8c1.4 2.8 3.8 5.1 6.6 6.6l2.2-2.2c.3-.3.7-.4 1-.2 1.1.4 2.3.6 3.600.6.6 0 1 .4 1 1V20c0 .6-.4 1-1 1C10.6 21 3 13.4 3 4c0-.6.4-1 1-1h3.5c.6 0 1 .4 1 1 0 1.3.2 2.5.6 3.6.1.3 0 .7-.2 1L6.6 10.8z"/></svg>
        0468 927 341
      </li>
      <li class="contact__item">
        <svg class="contact__icon" viewBox="0 0 24 24" aria-hidden="true"><rect x="2" y="5" width="20" height="14" fill="var(--accent)"/><path d="M2.5 5.5 12 13l9.5-7.5M2.5 18.5l7-6M21.5 18.5l-7-6" fill="none" stroke="#fff" stroke-width="1.5"/></svg>
        brennan@larkstone-partners.com.au
      </li>
      <li class="contact__item">
        <svg class="contact__icon" viewBox="0 0 24 24" aria-hidden="true"><circle cx="12" cy="12" r="10" fill="var(--accent)"/><path d="M6 7c2 0 3 1 3 3s2 2 2 4-1 3-1 5M15 4c-1 2 0 3 2 3s3 2 3 4" fill="none" stroke="#fff" stroke-width="1.8"/></svg>
        www.larkstone-partners.com.au
      </li>
    </ul>
  </div>
</section>

<section class="card card--back">
  <div class="brand">
    <span class="brand__dot"></span>
    <span class="brand__name">Larkstone Partners</span>
  </div>
  <p class="purpose">we shape the brightest teams <span class="purpose__accent">in every city</span></p>
</section>

</body>
</html>
```